Business card design needed

I am looking for a simple but elegant business card that has a professional and a classy look and feel about it. Must engage the persons attention.
I own and run multiple dental practices and offer basic to advanced dentistry.

Target Market(s)

people looking for dentists

Industry/Entity Type

Dental

Contact Information for Business Card

Dr. Desmond Falkner
Bellwood Dental
your smile our promise
Harlow Bay - 14 Tarvin Street Ph: 0741586297
Ashby - 52 Hollis Street Ph: 0741369014
Tallis - Shop 8 27 Corbett Drive Ph: 41628473
Email: df@bellwooddental.com.au

Requirements
Must have
• Contact Details
QR codes for easy storage and website redirection
email and web address

```html
<!DOCTYPE html>
<html lang="en">
<head>
<meta charset="utf-8">
<title>Bellwood Dental – Business Card</title>
<link href="https://fonts.googleapis.com/css2?family=Hind:wght@300;400;500&family=Tinos&display=swap" rel="stylesheet">
<style>
  :root{
    --backdrop:#6e6f70;
    --blue-deep:#1b8dd0;
    --blue-light:#3aaee2;
    --white:#ffffff;
    --pearl:#f7f8f8;
    --silver:#dcdddf;
    --ink:#2a2a2a;
    --icon-blue:#2f9bd8;
  }
  *{margin:0;padding:0;box-sizing:border-box}
  html,body{width:1200px;height:1140px;overflow:hidden;background:var(--backdrop)}
  .stage{position:relative;width:1159px;height:1100px;transform:scale(1.0354);transform-origin:0 0}
  .card{position:absolute;left:304px;width:550px;border-radius:30px;overflow:hidden}
  .card--front{top:104px;height:368px}
  .card--back{top:559px;height:369px}
  .card-art{position:absolute;inset:0;width:100%;height:100%}
  .brand-name{font-family:"Hind",sans-serif;font-weight:300;color:var(--white);white-space:nowrap}
  .tagline{font-family:"Tinos",serif;font-weight:400;color:var(--white);white-space:nowrap}
  .card--front .brand{position:absolute;left:0;right:0;top:112px;text-align:center}
  .card--front .brand-name{font-size:54px;letter-spacing:2.5px;line-height:1}
  .card--front .tagline{font-size:36px;line-height:1;margin-top:4px}
  .card--back .brand{position:absolute;left:34px;top:30px}
  .card--back .brand-name{font-size:25px;letter-spacing:1.5px;line-height:1}
  .card--back .tagline{font-size:15px;line-height:1;margin-top:1px}
  .email{position:absolute;right:22px;top:30px;display:flex;align-items:center;gap:8px;
    font-family:"Hind",sans-serif;font-size:11.5px;color:var(--white)}
  .email svg{width:13px;height:10px}
  .doctor{position:absolute;left:0;right:0;top:120px;text-align:center;font-family:"Tinos",serif;
    font-weight:400;font-size:37px;color:var(--white)}
  .locations{position:absolute;left:45px;top:278px;display:flex}
  .location{font-family:"Hind",sans-serif;font-size:11px;color:var(--ink);line-height:14px}
  .location:nth-child(1){width:179px}
  .location:nth-child(2){width:148px}
  .location .row{display:flex;gap:9px}
  .location .row + .row{margin-top:15px}
  .location svg{width:13px;height:13px;flex:none;fill:var(--icon-blue)}
  .city{font-weight:500}
</style>
</head>
<body>
<svg width="0" height="0" style="position:absolute">
  <defs>
    <radialGradient id="blueGlow" cx="50%" cy="45%" r="60%">
      <stop offset="0" stop-color="#3aaee2"/>
      <stop offset="1" stop-color="#1b8dd0"/>
    </radialGradient>
    <radialGradient id="pearlGlow" cx="50%" cy="60%" r="65%">
      <stop offset="0" stop-color="#f7f8f8"/>
      <stop offset="1" stop-color="#dcdddf"/>
    </radialGradient>
    <symbol id="icon-home" viewBox="0 0 16 16"><path d="M8 1 0 8h2.5v7h4v-5h3v5h4V8H16z"/></symbol>
    <symbol id="icon-phone" viewBox="0 0 16 16"><path d="M3.6 1.2 6 3.8 4.7 5.9c.9 2.2 2.6 4 4.9 5l2-1.4 2.6 2.4-1.6 2.6C6.9 14.3 1.6 9 1 3z"/></symbol>
  </defs>
</svg>

<div class="stage">
  <section class="card card--front">
    <svg class="card-art" viewBox="0 0 550 368" preserveAspectRatio="none" aria-hidden="true">
      <rect width="550" height="368" fill="url(#blueGlow)"/>
      <path d="M550 245C500 300 300 350 150 350C85 350 45 358 28 368L550 368Z" fill="url(#pearlGlow)"/>
    </svg>
    <div class="brand">
      <div class="brand-name">Bellwood Dental</div>
      <div class="tagline">your smile our promise</div>
    </div>
  </section>

  <section class="card card--back">
    <svg class="card-art" viewBox="0 0 550 369" preserveAspectRatio="none" aria-hidden="true">
      <rect width="550" height="369" fill="url(#blueGlow)"/>
      <path d="M0 263C8 240 80 232 180 232C330 232 500 210 550 162L550 369L0 369Z" fill="url(#pearlGlow)"/>
    </svg>
    <div class="brand">
      <div class="brand-name">Bellwood Dental</div>
      <div class="tagline">your smile our promise</div>
    </div>
    <div class="email">
      <svg viewBox="0 0 13 10" fill="none" stroke="#fff" stroke-width="1"><rect x=".5" y=".5" width="12" height="9"/><path d="M.5 .5 6.5 5.5 12.5 .5M.5 9.5 5 4.5M12.5 9.5 8 4.5"/></svg>
      <span>df@bellwooddental.com.au</span>
    </div>
    <h1 class="doctor">Dr. Desmond Falkner</h1>
    <div class="locations">
      <div class="location">
        <div class="row"><svg><use href="#icon-home"/></svg><div><div class="city">Harlow Bay</div><div>14 Tarvin Street</div></div></div>
        <div class="row"><svg><use href="#icon-phone"/></svg><div>0741586297</div></div>
      </div>
      <div class="location">
        <div class="row"><svg><use href="#icon-home"/></svg><div><div class="city">Ashby</div><div>52 Hollis Street</div></div></div>
        <div class="row"><svg><use href="#icon-phone"/></svg><div>0741369014</div></div>
      </div>
      <div class="location">
        <div class="row"><svg><use href="#icon-home"/></svg><div><div class="city">Tallis</div><div>Shop 8 27 Corbett Drive</div></div></div>
        <div class="row"><svg><use href="#icon-phone"/></svg><div>41628473</div></div>
      </div>
    </div>
  </section>
</div>
</body>
</html>
```